Vernac Law Business cards and stationary design project

We are looking for a stationary design for business cards (double sided), 8x10, 5x7, and legal and standard envelopes.

We would like the design to match the logo that we have already.
Color palate preferred is Teal, White, grey and any others that will look good for a professional law firm.

We would like this statement: "RELATIONSHIPS. RESPECT. RESULT" to be on the back of the business cards and maybe on the stationary if it looks good.

Please see link to website for more information: www.vernac-law.example

Target Market(s)

Potential clients that need Attorney services.

Industry/Entity Type

Law Firm

Contact Information for Business Card

We would like the front and back to be two different colors. Current business cards are teal front, grey back and are a vertical design. We are open to options with colors.

Font styles to use
Serif

Colors
33a6d7
33b8a4
b9b9b9
5c5c5c

Requirements
Must have
• Logo supplied needs to go on the card and stationary.
• Match website color palate, www.vernac-law.example
• Be professional and not too wordy.
• Criminal Law, Civil Litigation, Personal Injury, Restraining Orders need to be on the card.
Nice to have
• RELATIONSHIPS. RESPECT. RESULTS. on the back of the card.
Should not have
• Not be too busy/wordy or too flashy.

```html
<!DOCTYPE html>
<html lang="en">
<head>
<meta charset="utf-8">
<title>Vernac Law – Business Card</title>
<link rel="stylesheet" href="https://fonts.googleapis.com/css2?family=Open+Sans:wght@400;600&display=swap">
<style>
  :root {
    --backdrop: #000000;
    --card: #0b4244;
    --teal: #1c8f9c;
    --teal-bright: #2399a8;
    --white: #ffffff;
    --rule: #3d7f84;
    --icon: #6d9ea3;
  }
  * { margin: 0; padding: 0; box-sizing: border-box; }
  html, body {
    width: 1200px; height: 900px; overflow: hidden;
    background: var(--backdrop);
    font-family: "Open Sans", Arial, sans-serif;
  }
  .canvas { position: relative; width: 1200px; height: 900px; }
  .card {
    position: absolute; top: 271px; width: 457px; height: 281px;
    background: var(--card); border-radius: 14px; overflow: hidden;
  }
  .card--front { left: 137px; }
  .card--back { left: 626px; }

  .front-brand {
    position: absolute; left: 56px; top: 118px; width: 175px;
    text-align: center; color: var(--teal);
    font-size: 27px; font-weight: 600; line-height: 1;
  }
  .front-divider {
    position: absolute; left: 231px; top: 57px; width: 1px; height: 152px;
    background: var(--rule);
  }
  .details { position: absolute; left: 256px; top: 42px; color: var(--white); }
  .details__name { color: var(--teal-bright); font-size: 16.5px; font-weight: 600; line-height: 22px; }
  .details__title { font-size: 12.5px; line-height: 16px; }
  .details__address { margin-top: 12px; font-size: 12.5px; line-height: 14px; }
  .contact-list { list-style: none; margin-top: 19px; }
  .contact-list li {
    display: flex; align-items: center; height: 19px;
    font-size: 12.5px;
  }
  .contact-list svg { width: 10px; height: 10px; margin-right: 8px; fill: var(--icon); }
  .practice-areas {
    position: absolute; left: 0; right: 0; top: 225px;
    text-align: center; color: var(--white); font-size: 12.5px; line-height: 16px;
  }

  .back-brand {
    position: absolute; left: 0; right: 0; top: 150px;
    text-align: center; color: var(--teal);
    font-size: 30px; font-weight: 600; line-height: 1;
  }
  .tagline {
    position: absolute; left: 0; right: 0; top: 236px;
    display: flex; align-items: center; gap: 10px;
    color: var(--white); font-size: 12.5px; letter-spacing: 0.2px;
  }
  .tagline::before, .tagline::after {
    content: ""; flex: 1; height: 1px; background: var(--rule);
  }
</style>
</head>
<body>
<div class="canvas">
  <section class="card card--front">
    <div class="front-brand">Vernac Law</div>
    <div class="front-divider"></div>
    <div class="details">
      <div class="details__name">Marcus Ellery</div>
      <div class="details__title">Managing Director</div>
      <div class="details__address">12345, Address Goes Here<br>Country Name, 123456</div>
      <ul class="contact-list">
        <li><svg viewBox="0 0 10 10" aria-hidden="true"><path d="M2 0.5 L3.6 2.6 L2.8 3.6 Q4 6 6.4 7.2 L7.4 6.4 L9.5 8 L8.4 9.5 Q1.5 8 0.5 1.6 Z"/></svg>(044)-456-7890</li>
        <li><svg viewBox="0 0 10 10" aria-hidden="true"><path d="M2.5 1 H7 V3 H9 V9 H1 V3 H2.5 Z M3.5 2 V3 H6 V2 Z M3 5 H7 V6 H3 Z"/></svg>123-456-7890</li>
        <li><svg viewBox="0 0 10 10" aria-hidden="true"><path d="M0.5 2 H9.5 V8.5 H0.5 Z M1.2 2.6 L5 5.6 L8.8 2.6 Z" fill-rule="evenodd"/></svg>info@youremail.com</li>
        <li><svg viewBox="0 0 10 10" aria-hidden="true"><circle cx="5" cy="5" r="4.5"/></svg>www.website.com</li>
      </ul>
    </div>
    <p class="practice-areas">Practice areas, Criminal Law, Civil Litigation/Personal Injury<br>Restraining Orders</p>
  </section>

  <section class="card card--back">
    <div class="back-brand">Vernac Law</div>
    <p class="tagline">RELATIONSHIPS.&nbsp; RESPECT.&nbsp; RESULTS</p>
  </section>
</div>
</body>
</html>
```